Calm Harbor Bodywork business is seeking a Business Card Design

We are a new natural therapy business that needs a Business Card Design with an appointment card on the back.

We offer Myotherapy (muscle therapy) services and have a strong focus and commitment to helping people relieve pain and restore movement to their bodies.

I am attaching my business logo for you information.

Business card must contain my logo and have space for name, title, qualifications, phone number, email, web address

Appointment Card on the back of the card must contain space to write next appointment date, time and name of therapist and cancellation policy.

Cancellation Policy
Minimum of 24hrs notice is required prior to appointment time or full treatment fees with apply.

```html
<!DOCTYPE html>
<html lang="en">
<head>
<meta charset="utf-8">
<title>Calm Harbor Bodywork – Business Card</title>
<link href="https://fonts.googleapis.com/css2?family=Lato:wght@400;700;900&display=swap" rel="stylesheet">
<style>
  :root {
    --backdrop: #2b2b2b;
    --card: #fbfbfb;
    --ink: #3a3a3a;
    --ink-soft: #555555;
    --accent: #c41e2e;
    --box: #d6636c;
    --dots: #6a6a6a;
    --rule: #dddddd;
  }
  * { box-sizing: border-box; margin: 0; padding: 0; }
  html, body {
    width: 1200px; height: 900px; overflow: hidden;
    background: var(--backdrop);
    font-family: "Lato", sans-serif;
    color: var(--ink);
  }
  .card {
    position: absolute; left: 260px;
    width: 680px; height: 389px;
    background: var(--card);
    border-radius: 22px;
    box-shadow: 0 10px 30px rgba(0,0,0,.45);
  }
  .appointment-card { top: 40px; padding: 34px 48px; }
  .front-card { top: 470px; }

  .tag {
    display: inline-block;
    background: var(--accent); color: #fff;
    font-weight: 900; text-transform: uppercase;
    letter-spacing: 1px; padding: 3px 10px;
  }
  .tag-title { font-size: 22px; }
  .tag-policy { font-size: 17px; }
  .centered { text-align: center; }

  .field-row { display: flex; align-items: flex-end; gap: 10px; margin-top: 30px; font-size: 17px; }
  .field-label { text-transform: uppercase; color: var(--ink-soft); white-space: nowrap; }
  .field-label.strong { font-weight: 700; color: var(--ink); font-size: 19px; }
  .dotted { flex: 1; border-bottom: 3px dotted var(--dots); margin-bottom: 4px; }
  .ampm { display: flex; gap: 14px; font-size: 14px; color: var(--ink-soft); align-items: center; }

  .checkbox {
    display: inline-block; width: 26px; height: 22px;
    border: 2px solid var(--box); border-radius: 4px;
    vertical-align: middle; margin-left: 6px;
  }
  .ampm .checkbox { width: 20px; height: 17px; margin-left: 3px; }

  .days { display: flex; justify-content: space-between; margin-top: 30px; font-weight: 900; font-size: 20px; }

  .policy { margin-top: 26px; }
  .policy-text { margin-top: 10px; font-size: 17px; line-height: 1.35; color: var(--ink); }

  .person { position: absolute; left: 48px; top: 48px; width: 340px; }
  .person-name { color: var(--accent); font-weight: 900; font-size: 40px; letter-spacing: .5px; line-height: 1.05; }
  .person-role { font-weight: 700; font-size: 22px; letter-spacing: 1px; color: #222; margin-top: 4px; }
  .person-qualifications { font-size: 15px; color: var(--ink-soft); margin-top: 6px; }

  .contact-list {
    position: absolute; left: 48px; bottom: 44px; width: 340px;
    list-style: none; border-top: 2px solid var(--rule); padding-top: 16px;
  }
  .contact-item { display: flex; align-items: center; gap: 12px; font-size: 16px; margin-top: 9px; }
  .contact-item:first-child { margin-top: 0; }
  .contact-icon { width: 22px; height: 22px; flex: none; }

  .brand {
    position: absolute; right: 40px; top: 50%; transform: translateY(-50%);
    width: 240px; text-align: center;
  }
  .brand-mark { display: block; width: 110px; height: 110px; margin: 0 auto 16px; background: var(--accent); }
  .brand-name { color: var(--accent); font-weight: 700; font-size: 26px; line-height: 1.15; }
</style>
</head>
<body>
  <section class="card appointment-card">
    <div class="centered"><span class="tag tag-title">Next Appointment</span></div>

    <div class="field-row">
      <span class="field-label">Date:</span><span class="dotted"></span>
      <span class="field-label">Time:</span><span class="dotted"></span>
      <span class="ampm"><span>AM<span class="checkbox"></span></span><span>PM<span class="checkbox"></span></span></span>
    </div>

    <div class="days">
      <span>Mon<span class="checkbox"></span></span>
      <span>Tue<span class="checkbox"></span></span>
      <span>Wed<span class="checkbox"></span></span>
      <span>Thu<span class="checkbox"></span></span>
      <span>Fri<span class="checkbox"></span></span>
    </div>

    <div class="field-row">
      <span class="field-label strong">Name of Therapist:</span><span class="dotted"></span>
    </div>

    <div class="policy centered">
      <span class="tag tag-policy">Cancellation Policy</span>
      <p class="policy-text">Minimum of 24hrs notice is required prior to appointment time or full<br>treatment fees with apply</p>
    </div>
  </section>

  <section class="card front-card">
    <div class="person">
      <div class="person-name">YOUR NAME</div>
      <div class="person-role">DESIGNATION</div>
      <div class="person-qualifications">Qualifications</div>
    </div>

    <ul class="contact-list">
      <li class="contact-item">
        <svg class="contact-icon" viewBox="0 0 24 24"><path fill="#c41e2e" d="M6.6 10.8a15.2 15.2 0 0 0 6.6 6.6l2.2-2.2a1 1 0 0 1 1-.25 11.4 11.4 0 0 0 3.6.57 1 1 0 0 1 1 1V20a1 1 0 0 1-1 1A17 17 0 0 1 3 4a1 1 0 0 1 1-1h3.5a1 1 0 0 1 1 1c0 1.25.2 2.45.57 3.57a1 1 0 0 1-.25 1z"/></svg>
        <span>0400 000 000</span>
      </li>
      <li class="contact-item">
        <svg class="contact-icon" viewBox="0 0 24 24"><rect x="2" y="5" width="20" height="14" rx="2" fill="#c41e2e"/><path d="M3 6l9 7 9-7" fill="none" stroke="#fff" stroke-width="1.8"/></svg>
        <span>hello@calmharborbodywork.com</span>
      </li>
      <li class="contact-item">
        <svg class="contact-icon" viewBox="0 0 24 24"><circle cx="12" cy="12" r="10" fill="#c41e2e"/><path d="M2 12h20M12 2c3 3 3 17 0 20M12 2c-3 3-3 17 0 20" fill="none" stroke="#fff" stroke-width="1.4"/></svg>
        <span>www.calmharborbodywork.com</span>
      </li>
    </ul>

    <div class="brand">
      <span class="brand-mark"></span>
      <span class="brand-name">Calm Harbor Bodywork</span>
    </div>
  </section>
</body>
</html>
```